Visitenkarten/Briefpaier/Kassenkassenbelege für Juwelier
Zielgruppe
Mittelständischer Juwelier mit zwei Filialen. Klassischer Schmuck, Uhren und Modeschmuck
Aufgabenstellung
Es müssen für zwei Geschäfte Visitenkarten, Briefpapier (A4) und Kassenkassenbelege (A6) erstellt werden. Logo und Typo im Anhang. Ein Farbkonzept besteht noch nicht. Die Idee geht in Richtung Bordeaux-Rot.
Generell:
(1) Sieht erstmal nach viel Beschreibung aus, bitte nicht entmutigen lassen, sind zu 90% nur austauschbare Inhalts-/Kontaktdaten.
(2) Für meine Zwecke reicht es vollkommen aus, wenn bei den Vorschlägen zur Arbeitsersparnis erstmal nur mit einer Adresse gearbeitet wird. Wenn ich dann den zutreffenden Designvorschlag gefunden habe, können wir die zweite Adresse in dem ersten Format umsetzen. Ich denke das spart Zeit und Nerven.
(3) Bitte Angaben wie "Tel.:" oder "USt.- ID:" nicht wörtlich nehmen, es soll dabei klar sein worum es geht; wenn "Telefon" ausgeschrieben besser aussieht, bitte in der optisch ansprechenderen Form verwenden.
(4) Bei Fragen, bitte fragen!
(5) Viel Spass bei dem Projekt - Ich freu' mich auf die Vorschläge!
Visitenkarten(1):
Juwelier Brenneck GmbH
www.juwelier-brenneck-beispiel.de
Visitenkarten(2):
Visitenkarten(generell):
(1) Die einzelnen Daten können durch Hervorhebungen wie Adresse, Kontakt, Online/Internet unterteilt bzw. hervorgehoben werden.
(2) Die Visitenkarten sollen farbig gedruckt werden; geplant ist weiß als Hintergrund ist aber nicht zwingend bei einer guten anderen Idee
Briefpapier:
(1)Absender im Adressfeld für DIN-lang Briefumschläge mit Fenster:
(2)Informationen im Footer/Seitenbereich:
Juwelier Brenneck Gmb..

```html
<!DOCTYPE html>
<html lang="de">
<head>
<meta charset="utf-8">
<title>Juwelier Brenneck – Visitenkarte</title>
<link rel="stylesheet" href="https://fonts.googleapis.com/css2?family=Source+Sans+3:wght@400;600&display=swap">
<style>
  :root {
    --page-bg: #b0b0ad;
    --card-bg: #f7f7f6;
    --brand-grey: #9e9e9b;
    --brand-bordeaux: #4a2236;
    --text-dark: #4a2a3a;
    --text-grey: #9a9a98;
  }
  html, body {
    margin: 0;
    width: 1200px;
    height: 800px;
    overflow: hidden;
    background: var(--page-bg);
    font-family: "Source Sans 3", "Source Sans Pro", sans-serif;
  }
  .stage {
    width: 1200px;
    height: 800px;
    display: flex;
    align-items: center;
    justify-content: center;
  }
  .business-card {
    position: relative;
    width: 680px;
    height: 440px;
    background: var(--card-bg);
    box-shadow: 0 10px 30px rgba(0,0,0,0.12);
  }
  .logo-band {
    position: absolute;
    left: 200px;
    top: 92px;
    width: 180px;
    height: 74px;
    background: var(--brand-grey);
  }
  .card-text {
    position: absolute;
    left: 200px;
    top: 198px;
    line-height: 1.3;
    font-size: 21px;
    color: var(--text-dark);
  }
  .company-name {
    margin: 0 0 2px;
    font-size: 19px;
    font-weight: 600;
    letter-spacing: 0.06em;
    text-transform: uppercase;
    color: var(--text-grey);
  }
  .company-name .legal { text-transform: none; letter-spacing: 0.02em; }
  .card-text p { margin: 0; }
  .label { color: var(--text-grey); }
  .email { color: var(--text-grey); }
  .accent-square {
    position: absolute;
    right: 0;
    bottom: 96px;
    width: 38px;
    height: 44px;
    background: var(--brand-bordeaux);
  }
</style>
</head>
<body>
  <main class="stage">
    <article class="business-card">
      <div class="logo-band"></div>
      <div class="card-text">
        <h1 class="company-name">Juwelier Brenneck <span class="legal">GmbH</span></h1>
        <p class="address">Musterweg 12 in 45100 Beispielstadt</p>
        <p class="contact"><span class="label">TEL</span> 0201-555010&nbsp; <span class="label">FAX</span> 0201-555011&nbsp; <span class="email">info@juwelier-brenneck-beispiel.de</span></p>
        <p class="web">www.juwelier-brenneck-beispiel.de</p>
      </div>
      <div class="accent-square"></div>
    </article>
  </main>
</body>
</html>
```